Design a New Business Card for Our Company

We are looking for fresh, unique, and a modern business card that reflects our roots as digital marketing agency focused on SEM.

Industry/Entity Type

Marketing

Contact Information for Business Card

looking for very unique out of the box designs. clean and modern that compliments our logo

Requirements
Must have
• colors should match our logo
• Front should have name, address, email, and phone/fax of the person, phone/fax are the same number
• back should have our url

```html
<!DOCTYPE html>
<html lang="en">
<head>
<meta charset="utf-8">
<title>Clearpath Digital – Business Card</title>
<link href="https://fonts.googleapis.com/css2?family=Open+Sans:wght@400;600;700&display=swap" rel="stylesheet">
<style>
  :root {
    --page-bg: #e6e7ea;
    --card-bg: #ffffff;
    --brand-blue: #4a86cc;
    --pattern-grey: #ececee;
    --pattern-blue: #e3e8f6;
    --text-grey: #8a8d92;
    --rule-grey: #b9bcc1;
    --shadow: rgba(0, 0, 0, 0.18);
  }
  * { margin: 0; padding: 0; box-sizing: border-box; }
  html, body {
    width: 1200px; height: 900px; overflow: hidden;
    background: var(--page-bg);
    font-family: "Open Sans", Arial, sans-serif;
  }
  .canvas { position: relative; width: 1200px; height: 900px; }
  .card {
    position: absolute; left: 250px; width: 700px; height: 400px;
    background: var(--card-bg);
    box-shadow: 0 8px 24px var(--shadow);
    overflow: hidden;
  }
  .card--back { top: 40px; }
  .card--front { top: 470px; }

  .pattern-area {
    position: absolute;
    background:
      radial-gradient(ellipse at 65% 40%, var(--pattern-blue) 0%, rgba(227,232,246,0) 60%),
      radial-gradient(ellipse at 35% 60%, var(--pattern-grey) 0%, rgba(236,236,238,0) 65%);
  }
  .card--back .pattern-area { left: 90px; top: 20px; width: 520px; height: 380px; }
  .card--front .pattern-area { left: 170px; top: 200px; width: 290px; height: 200px; }

  .wordmark {
    position: relative;
    display: flex; align-items: center; gap: 10px;
    color: var(--brand-blue); font-weight: 600; letter-spacing: -0.5px;
    white-space: nowrap;
  }
  .wordmark__dot {
    width: 0.6em; height: 0.6em; border-radius: 50%;
    background: var(--brand-blue);
  }

  .card--back .wordmark {
    position: absolute; top: 150px; left: 0; right: 0;
    justify-content: center; font-size: 46px;
  }
  .card--back .site-url {
    position: absolute; bottom: 40px; left: 0; right: 0;
    text-align: center; color: var(--brand-blue); font-size: 20px;
  }

  .card--front .wordmark {
    position: absolute; top: 150px; left: 40px; font-size: 29px;
  }
  .top-rule {
    position: absolute; top: 78px; left: 360px; right: 0;
    height: 1.5px; background: var(--rule-grey);
  }
  .contact { position: absolute; top: 88px; left: 365px; right: 20px; }
  .contact__name { color: var(--brand-blue); font-size: 21px; font-weight: 700; line-height: 1.2; }
  .contact__role { color: var(--text-grey); font-size: 15px; margin-left: 22px; }
  .contact__divider { width: 190px; height: 1.5px; background: var(--rule-grey); margin: 12px 0 14px; }
  .contact__company { color: var(--brand-blue); font-size: 16px; }
  .contact__address { color: var(--text-grey); font-size: 15px; line-height: 1.3; }
  .contact__list { list-style: none; margin-top: 16px; }
  .contact__item {
    display: flex; align-items: center; gap: 9px;
    color: var(--text-grey); font-size: 15px; line-height: 1.45;
  }
  .icon { width: 17px; height: 17px; flex: none; }
</style>
</head>
<body>
<main class="canvas">

  <section class="card card--back" aria-label="Card back">
    <div class="pattern-area" role="img" aria-label="Soft pattern of grey and pale blue circles"></div>
    <div class="wordmark"><span class="wordmark__dot"></span>Clearpath Digital</div>
    <p class="site-url">www.clearpathdigital.com</p>
  </section>

  <section class="card card--front" aria-label="Card front">
    <div class="pattern-area" role="img" aria-label="Soft pattern of grey and pale blue circles"></div>
    <div class="wordmark"><span class="wordmark__dot"></span>Clearpath Digital</div>
    <div class="top-rule"></div>
    <div class="contact">
      <p class="contact__name">Owen Hartley</p>
      <p class="contact__role">Owner</p>
      <div class="contact__divider"></div>
      <p class="contact__company">Clearpath Digital</p>
      <p class="contact__address">N. 4 Maple Row, Suite 210,<br>Riverton, OR 55555</p>
      <ul class="contact__list">
        <li class="contact__item">
          <svg class="icon" viewBox="0 0 20 20" aria-hidden="true"><circle cx="10" cy="10" r="10" fill="#4a86cc"/><path d="M6 6.5c0 4 3.5 7.5 7.5 7.5l1-2-2-1-1 1c-1.3-.6-2.4-1.7-3-3l1-1-1-2z" fill="#fff"/></svg>
          987.654.321
        </li>
        <li class="contact__item">
          <svg class="icon" viewBox="0 0 20 20" aria-hidden="true"><circle cx="10" cy="10" r="10" fill="#4a86cc"/><rect x="5" y="8" width="10" height="6" rx="1" fill="#fff"/><rect x="7" y="5" width="6" height="3" fill="#fff"/></svg>
          987.654.321
        </li>
        <li class="contact__item">
          <svg class="icon" viewBox="0 0 20 20" aria-hidden="true"><circle cx="10" cy="10" r="10" fill="#4a86cc"/><rect x="5" y="6.5" width="10" height="7" fill="#fff"/><path d="M5 6.5l5 4 5-4" fill="none" stroke="#4a86cc" stroke-width="1.2"/></svg>
          hello@clearpathdigital.com
        </li>
        <li class="contact__item">
          <svg class="icon" viewBox="0 0 20 20" aria-hidden="true"><circle cx="10" cy="10" r="10" fill="#4a86cc"/><circle cx="10" cy="10" r="5" fill="none" stroke="#fff" stroke-width="1.2"/><path d="M5 10h10M10 5c-2 3-2 7 0 10M10 5c2 3 2 7 0 10" fill="none" stroke="#fff" stroke-width="1"/></svg>
          www.clearpathdigital.com
        </li>
      </ul>
    </div>
  </section>

</main>
</body>
</html>
```